Quote Cards With KB May 2025 for Instagram

I would like to put these quotes over one of the pictures attached; Instagram (new size: 4:5 (1080 x 1350 pixels) One Quote per picture, and I want the quote to be bold or easy to read as well. I provided a few reference graphics that I really like as examples below. In very small letters at the bottom add @KBHarlowOnline

All of the pictures are attached; you can pick any photo and add one quote to it; but no stock photography

```html
<!DOCTYPE html>
<html lang="en">
<head>
<meta charset="utf-8">
<title>Quote Cards With KB – May 2025</title>
<link href="https://fonts.googleapis.com/css2?family=Oswald:wght@500;600&family=Roboto+Condensed:wght@300;400;700&family=Poppins:wght@600;700&display=swap" rel="stylesheet">
<style>
  :root{
    --page:#f2f2f2;
    --white:#ffffff;
    --ink:#111111;
    --cream:#ffeab0;
    --handle-bg:rgba(255,255,255,0.28);
  }
  *{box-sizing:border-box;margin:0;padding:0}
  html,body{width:1200px;height:3217px;overflow:hidden;background:var(--page)}
  .sheet{position:relative;width:1200px;height:3217px}
  .card{position:absolute;width:461px;height:576px;overflow:hidden}
  .col-left{left:120px}.col-right{left:621px}
  .row-1{top:81px}.row-2{top:692px}.row-3{top:1308px}.row-4{top:1930px}.row-5{top:2562px}
  .photo{position:absolute;inset:0}
  .panel{position:absolute;inset:0}
  .copy,.cta-line{position:absolute;color:var(--white);text-shadow:0 2px 6px rgba(0,0,0,.35);white-space:nowrap}
  .headline{font-family:"Oswald",sans-serif;font-weight:500;line-height:1.08;letter-spacing:-0.5px}
  .sub{font-family:"Roboto Condensed",sans-serif;font-weight:400;line-height:1.3}
  .light{font-weight:300}
  .bold{font-weight:700}
  .cta{font-family:"Poppins",sans-serif;font-weight:600}
  .handle{position:absolute;bottom:12px;height:20px;width:190px;background:var(--handle-bg);
    font-family:"Poppins",sans-serif;font-weight:600;font-size:14px;color:var(--white);
    line-height:20px;padding-left:22px;white-space:nowrap}
  .handle.on-right{right:0}.handle.on-left{left:0}

  .card-tired .photo{background:linear-gradient(160deg,#5a2a6e,#c03a8a 60%,#3a1f4d)}
  .card-tired .panel{background:linear-gradient(135deg,#a02cae,#6a3fc8 55%,#4632b8);clip-path:polygon(0 0,58% 0,72% 55%,53% 100%,0 100%)}
  .card-weight .photo{background:linear-gradient(180deg,#2b2f4a,#6b4b2a 50%,#d9a22a)}
  .card-weight .panel{background:linear-gradient(135deg,#6b4a1e,#c98f1a 55%,#e2a52a);clip-path:polygon(0 0,63% 0,56% 45%,62% 100%,0 100%)}
  .card-hormonal .photo{background:linear-gradient(180deg,#9fcff0,#b9c7bf 45%,#4d5a3a)}
  .card-hormonal .panel{background:linear-gradient(160deg,#6aa43c,#3a4e32 55%,#2c2c2c);clip-path:polygon(38% 0,100% 0,100% 100%,48% 100%,39% 50%)}
  .card-after40 .photo{background:linear-gradient(180deg,#1d2233,#3a3f55 50%,#23232c)}
  .card-after40 .panel{background:linear-gradient(170deg,#5a3d2a,#3d2a20 60%,#2a211c);clip-path:polygon(45% 0,100% 0,100% 100%,47% 100%,41% 52%)}
  .card-flat .photo{background:linear-gradient(180deg,#d9d9d9,#bfbfbf 55%,#4a4a4a)}
  .card-flat .panel{background:linear-gradient(160deg,#555,#2e2e2e 60%,#1f1f1f);clip-path:polygon(0 0,64% 0,45% 40%,56% 100%,0 100%)}
  .card-bloating .photo{background:linear-gradient(180deg,#ececef,#d8d8de 50%,#2a2a2e)}
  .card-bloating .panel{background:linear-gradient(160deg,#f4f4f4,#e4e4e8 60%,#cfd0da);clip-path:polygon(0 0,48% 0,60% 45%,49% 100%,0 100%)}
  .card-bloating .copy,.card-bloating .cta-line{color:var(--ink);text-shadow:none}
  .card-bloating .handle{background:rgba(255,255,255,.75);color:var(--ink)}
  .card-right .photo{background:linear-gradient(180deg,#c9b28a,#b07a70 50%,#8a6a2a)}
  .card-right .panel{background:linear-gradient(170deg,#e6a53a,#d27a5a 50%,#b8566e);clip-path:polygon(42% 0,100% 0,100% 100%,45% 100%,46% 40%)}
  .card-right .copy,.card-plan .copy,.card-plan .cta-line{color:var(--cream)}
  .card-plan .photo{background:linear-gradient(180deg,#2a3a8a,#6a4a7a 50%,#2a2a3a)}
  .card-plan .panel{background:linear-gradient(160deg,#b04aa8,#6a3ac8 45%,#3a36c4);clip-path:polygon(37% 0,100% 0,100% 100%,42% 100%,44% 55%)}
  .card-plan .handle{background:rgba(214,80,170,.85)}
  .card-secret .photo{background:linear-gradient(180deg,#a9cdf0,#8aa9c4 50%,#2a2a2a)}
  .card-secret .panel{background:linear-gradient(160deg,#6a4a34,#4a3426 60%,#2e231c);clip-path:polygon(0 0,50% 0,64% 50%,60% 100%,0 100%)}
  .card-30s .photo{background:linear-gradient(180deg,#6a6a6e,#3c3c40 50%,#1e1e22)}
  .card-30s .panel{background:linear-gradient(160deg,#5a3d2e,#3d2c24 60%,#2a221e);clip-path:polygon(0 0,57% 0,52% 48%,56% 100%,0 100%)}
</style>
</head>
<body>
<main class="sheet">

  <section class="card card-tired col-left row-1">
    <div class="photo" role="img" aria-label="KB standing on stage in a pink gown"></div>
    <div class="panel"></div>
    <div class="copy" style="left:18px;top:30px">
      <p class="headline" style="font-size:54px;line-height:1.22">Tired.<br>Moody.<br>Stubborn<br>Belly Fat.</p>
      <p class="sub" style="font-size:33px;margin-top:22px;line-height:1.38">Your hormones<br>are screaming<br>for help!</p>
    </div>
    <p class="cta cta-line" style="left:20px;top:500px;font-size:26px">Let’s fix that.</p>
    <div class="handle on-right">@KBHarlowOnline</div>
  </section>

  <section class="card card-weight col-right row-1">
    <div class="photo" role="img" aria-label="KB on a basketball court in a brown top and black jeans"></div>
    <div class="panel"></div>
    <div class="copy" style="left:18px;top:34px">
      <p class="headline" style="font-size:45px;line-height:1.33">That stubborn<br>weight?<br>It’s not your<br>fault</p>
      <p class="sub" style="font-size:32px;margin-top:18px;line-height:1.4">Your hormones<br>are to blame<br>and you’re not<br>alone;</p>
    </div>
    <p class="cta cta-line" style="left:22px;top:519px;font-size:22px">But there is a fix.</p>
    <div class="handle on-right">@KBHarlowOnline</div>
  </section>

  <section class="card card-hormonal col-left row-2">
    <div class="photo" role="img" aria-label="KB outdoors in a black outfit on a hillside"></div>
    <div class="panel"></div>
    <div class="copy" style="left:229px;top:34px">
      <p class="headline" style="font-size:45px;line-height:1.4">Your belly<br>isn’t fat…<br>it’s hormonal.</p>
      <p class="sub" style="font-size:35px;margin-top:6px;line-height:1.4">And here’s<br>how to fix it.</p>
      <p class="sub light" style="font-size:34px;line-height:1.4">Comment</p>
      <p class="sub" style="font-size:38px;line-height:1.3">HORMONES</p>
      <p class="sub light" style="font-size:34px;line-height:1.35">if nothing is<br>working.</p>
    </div>
    <div class="handle on-left">@KBHarlowOnline</div>
  </section>

  <section class="card card-after40 col-right row-2">
    <div class="photo" role="img" aria-label="KB in a sheer black outfit by a night city window"></div>
    <div class="panel"></div>
    <div class="copy" style="left:228px;top:28px">
      <p class="headline" style="font-size:42px;line-height:1.25">The stubborn</p>
      <p class="headline" style="font-size:72px;line-height:1.08">belly fat</p>
      <p class="headline" style="font-size:44px;line-height:1.15">after 40?</p>
      <p class="sub" style="font-size:33px;margin-top:20px;line-height:1.38">It’s not about<br>calories;<br>it’s about your<br>hormones.</p>
    </div>
    <p class="cta cta-line" style="left:230px;top:512px;font-size:27px">Here is the fix!</p>
    <div class="handle on-left">@KBHarlowOnline</div>
  </section>

  <section class="card card-flat col-left row-3">
    <div class="photo" role="img" aria-label="KB posing in a sheer striped top indoors"></div>
    <div class="panel"></div>
    <div class="copy" style="left:28px;top:34px">
      <p class="headline" style="font-size:50px;line-height:1.25">Flat tummy<br>in your<br>40s?</p>
      <p class="sub" style="font-size:30px;margin-top:14px;line-height:1.36">It’s still<br>possible!<br>Comment</p>
      <p class="sub" style="font-size:42px;line-height:1.2">BYE BELLY</p>
      <p class="sub" style="font-size:30px;line-height:1.36">to get the 10<br>secrets to a<br>flatter tummy</p>
    </div>
    <div class="handle on-right">@KBHarlowOnline</div>
  </section>

  <section class="card card-bloating col-right row-3">
    <div class="photo" role="img" aria-label="KB in a white cropped sweater pointing upward"></div>
    <div class="panel"></div>
    <div class="copy" style="left:19px;top:72px">
      <p class="headline" style="font-size:48px;line-height:1.2">Bloating.</p>
      <p class="headline" style="font-size:45px;line-height:1.2">Muffin top.</p>
      <p class="headline" style="font-size:40px;line-height:1.2">Puffy waistline.</p>
      <p class="sub" style="font-size:35px;margin-top:4px;line-height:1.35">Your body’s<br>screaming for<br>a different<br>kind of fix</p>
    </div>
    <p class="cta cta-line" style="left:20px;top:490px;font-size:27px">Here it is</p>
    <div class="handle on-right">@KBHarlowOnline</div>
  </section>

  <section class="card card-right col-left row-4">
    <div class="photo" role="img" aria-label="KB in a pink dress beside a sunflower display"></div>
    <div class="panel"></div>
    <div class="copy" style="left:234px;top:54px">
      <p class="headline" style="font-size:36px;line-height:1.36">You’re doing<br>all the “right”<br>things, but your<br>belly won’t go<br>down?</p>
      <p class="sub" style="font-size:38px;margin-top:26px;line-height:1.4">Here’s what<br>you haven’t<br>tried.</p>
    </div>
    <div class="handle on-left">@KBHarlowOnline</div>
  </section>

  <section class="card card-plan col-right row-4">
    <div class="photo" role="img" aria-label="KB courtside at a basketball game holding a ball"></div>
    <div class="panel"></div>
    <div class="copy" style="left:228px;top:40px">
      <p class="headline" style="font-size:34px;line-height:1.38">This 90-day plan<br>helped women</p>
      <p class="headline" style="font-size:30px;line-height:1.3">over 40 slim down,</p>
      <p class="sub" style="font-size:40px;margin-top:36px;line-height:1.3">Get a tiny<br>waist and<br>feel sexy<br>again.</p>
    </div>
    <p class="cta cta-line" style="left:228px;top:512px;font-size:27px">You’re next.</p>
    <div class="handle on-left">@KBHarlowOnline</div>
  </section>

  <section class="card card-secret col-left row-5">
    <div class="photo" role="img" aria-label="KB smiling outdoors in a black top under a blue sky"></div>
    <div class="panel"></div>
    <div class="copy" style="left:18px;top:80px">
      <p class="headline" style="font-size:35px;line-height:1.23">This is the secret<br>women over 40<br>are using to get<br>snatched; without<br>starving.</p>
      <p class="sub" style="font-size:33px;margin-top:22px;margin-left:4px;line-height:1.4">Comment</p>
      <p class="sub bold" style="font-size:52px;margin-left:4px;line-height:1.15">SKINNY</p>
      <p class="sub" style="font-size:33px;margin-left:4px;line-height:1.35">to get the<br>exact plan.</p>
    </div>
    <div class="handle on-right">@KBHarlowOnline</div>
  </section>

  <section class="card card-30s col-right row-5">
    <div class="photo" role="img" aria-label="KB in a black open-back outfit looking over her shoulder"></div>
    <div class="panel"></div>
    <div class="copy" style="left:20px;top:36px">
      <p class="headline" style="font-size:45px;line-height:1.16">What<br>worked in<br>your 30s<br>won’t work<br>now.</p>
      <p class="sub" style="font-size:33px;margin-top:8px;line-height:1.33">Here’s what<br>actually does.<br>Drop 30<br>Pounds in<br>3 Months.</p>
    </div>
    <div class="handle on-right">@KBHarlowOnline</div>
  </section>

</main>
</body>
</html>
```